Business Card Design

I'm a commercial general contractor remodel offices, hotels, health clubs and stores mostly San Francisco and the peninsula
the file I down loaded is kind of what I want I like the I beam with my company name in it, that would be fine with me but if you have better Idea will look at it you never know, I'm decided to give in and change my company name to how every one knows me, I have been in business since 1991, I like the I beam logo I included one of my old card from my old company for reference for you.

BROCK CONSTRUCTION (is my company name)
Warren Pelkey contractor, LIc 514387
3148 Larkspur Row, San Bruno, California 94071
mobile, (415) 736-4052
phone (650) 514-2087
Fax, (650) 514-2088
email, brock@brockconstruction.example

```html
<!DOCTYPE html>
<html lang="en">
<head>
<meta charset="utf-8">
<title>Brock Construction – Business Card</title>
<link href="https://fonts.googleapis.com/css2?family=Source+Sans+3:wght@400;600&display=swap" rel="stylesheet">
<style>
  :root {
    --page: #ffffff;
    --card: #ffffff;
    --ink: #1d1d1d;
    --band: #1c1c1c;
    --blue: #4f9be8;
    --grey: #6b6b6b;
    --band-text: #d9d9d9;
  }
  * { box-sizing: border-box; margin: 0; padding: 0; }
  html, body {
    width: 1200px; height: 800px; overflow: hidden;
    background: var(--page);
    font-family: "Source Sans 3", "Source Sans Pro", sans-serif;
  }
  .card {
    position: absolute; left: 180px; top: 160px;
    width: 840px; height: 480px;
    background: var(--card);
    box-shadow: 0 6px 24px rgba(0,0,0,.12);
    overflow: hidden;
  }
  .brand {
    position: absolute; left: 70px; top: 90px;
    display: flex; align-items: center; gap: 14px;
    color: var(--ink);
  }
  .brand-mark { width: 22px; height: 22px; background: var(--blue); }
  .brand-name {
    font-weight: 600; font-size: 30px; letter-spacing: 3px; line-height: 1.1;
    color: var(--blue);
  }
  .name-bar, .title-bar {
    position: absolute; right: 0;
    background: var(--blue); color: #fff;
    text-transform: uppercase; display: flex; align-items: center;
  }
  .name-bar {
    left: 420px; top: 150px; height: 56px;
    padding-left: 28px; font-size: 32px; font-weight: 400; letter-spacing: .5px;
  }
  .title-bar {
    left: 480px; top: 214px; height: 44px;
    padding-left: 28px; font-size: 26px; letter-spacing: .5px;
  }
  .contacts {
    position: absolute; left: 500px; top: 276px;
    list-style: none;
  }
  .contacts li {
    display: flex; align-items: center; gap: 22px;
    height: 30px; font-size: 24px; color: var(--grey); letter-spacing: 1px;
  }
  .contacts svg { width: 20px; height: 20px; fill: var(--ink); }
  .band {
    position: absolute; left: 0; right: 0; top: 380px; height: 76px;
    background: var(--band); color: var(--band-text);
    display: flex; flex-direction: column; justify-content: center; align-items: flex-end;
    padding-right: 30px; font-size: 17px; line-height: 1.45;
  }
</style>
</head>
<body>
  <main class="card">
    <div class="brand">
      <span class="brand-mark"></span>
      <span class="brand-name">BROCK<br>CONSTRUCTION</span>
    </div>

    <div class="name-bar">Warren Pelkey</div>
    <div class="title-bar">Contractor</div>

    <ul class="contacts">
      <li>
        <svg viewBox="0 0 20 20" aria-label="mobile"><rect x="5" y="1" width="10" height="18" rx="2"/><rect x="7" y="4" width="6" height="10" fill="#fff"/></svg>
        (415) 736-4052
      </li>
      <li>
        <svg viewBox="0 0 20 20" aria-label="phone"><circle cx="10" cy="10" r="9"/><path d="M7 5c-1 1-1 3 1 6s4 4 5 4l1-1-2-2-1 1c-1-.5-2-2-2.5-3l1-1-1.5-3z" fill="#fff"/></svg>
        (650) 514-2087
      </li>
      <li>
        <svg viewBox="0 0 20 20" aria-label="fax"><rect x="2" y="7" width="16" height="11" rx="1"/><rect x="5" y="2" width="10" height="7" fill="#fff" stroke="#1d1d1d" stroke-width="1.5"/><rect x="5" y="12" width="10" height="2" fill="#fff"/></svg>
        (650) 514-2088
      </li>
    </ul>

    <div class="band">
      <span class="email">brock@brockconstruction.example</span>
      <span class="address">Lic 514387, 3148 Larkspur Row , San Bruno, California 94071</span>
    </div>
  </main>
</body>
</html>
```